Business Card Update, need to bring life to the card, two sided color

We need a new business card design, are moving and changing addresses and need a new look, we have the logos already attached but need a new style moving forward. Can incorporate the color of the logo (The Green) as well, maybe a solid back? We deal with safety products revolving around static electricity and safety lighting. Would like to keep same font in second logo as well.

Target Market(s)

Electrical Safety, Lighting

Contact Information for Business Card

Dale Fenwick
Vice President
Office: 770-555-4821
Cell: 770-555-3067
dale@tkfenwick.example
www.tkfenwick.example
4700 West Harbor Boulevard
Suite #150
Roswell, GA 30076

Font styles to use
Serif
Sans Serif

Requirements
Must have
• Since 1918
Nice to have
• Could use the 100 Year Logo for back of card, would like the back of card to be the same green as logo.
Should not have
• No black cards please.

```html
<!DOCTYPE html>
<html lang="en">
<head>
<meta charset="utf-8">
<title>T.K. Fenwick Business Card</title>
<link rel="stylesheet" href="https://fonts.googleapis.com/css2?family=Lato:wght@400;700&family=Arimo:wght@700&display=swap">
<style>
  :root {
    --brand-green: #02995a;
    --paper: #ffffff;
    --ink: #1d1d1d;
    --backdrop: #d6d6d6;
  }
  * { margin: 0; padding: 0; box-sizing: border-box; }
  html, body { width: 1200px; height: 802px; overflow: hidden; }
  body { background: var(--backdrop); position: relative; }

  .card {
    position: absolute;
    top: 274px;
    width: 442px;
    height: 265px;
    overflow: hidden;
  }
  .card-front { left: 136px; background: var(--paper); }
  .card-back { left: 624px; background: var(--brand-green); }

  .front-mark {
    position: absolute;
    left: -9px; top: 6px;
    width: 250px; height: 250px;
    border-radius: 50%;
    background: var(--brand-green);
    display: flex; flex-direction: column; align-items: center; justify-content: center;
    gap: 4px;
  }
  .front-mark-name {
    font-family: "Lato", sans-serif;
    font-weight: 700;
    font-size: 26px;
    color: var(--paper);
    padding-left: 10px;
  }
  .front-mark-since {
    font-family: "Lato", sans-serif;
    font-weight: 700;
    font-size: 12px;
    letter-spacing: 2px;
    text-transform: uppercase;
    color: var(--paper);
    padding-left: 10px;
  }

  .contact {
    position: absolute;
    right: 29px; top: 44px;
    text-align: right;
    font-family: "Lato", sans-serif;
    color: var(--ink);
    font-size: 12.5px;
    line-height: 16px;
  }
  .contact-name {
    font-weight: 700;
    font-size: 16.5px;
    color: var(--brand-green);
    line-height: 18px;
    text-transform: uppercase;
  }
  .contact-title { margin-bottom: 12px; }
  .contact-line { display: flex; justify-content: flex-end; align-items: center; gap: 3px; }
  .contact-line svg { width: 10px; height: 10px; fill: var(--brand-green); flex: none; }
  .contact-address { margin-top: 12px; }

  .back-lockup {
    position: absolute;
    left: 80px; top: 97px;
    display: flex; align-items: center; gap: 8px;
  }
  .back-circle {
    width: 70px; height: 70px;
    border-radius: 50%;
    background: var(--paper);
    flex: none;
  }
  .back-name {
    font-family: "Arimo", sans-serif;
    font-weight: 700;
    color: var(--paper);
    font-size: 23px;
    line-height: 24px;
  }
  .back-tagline {
    font-family: "Arimo", sans-serif;
    font-weight: 700;
    color: var(--paper);
    font-size: 11.5px;
    line-height: 15px;
    padding-left: 15px;
    letter-spacing: 0.3px;
  }
</style>
</head>
<body>
  <section class="card card-front">
    <div class="front-mark">
      <span class="front-mark-name">T.K. Fenwick</span>
      <span class="front-mark-since">Since 1918</span>
    </div>
    <div class="contact">
      <p class="contact-name">Dale Fenwick</p>
      <p class="contact-title">Vice President</p>
      <p class="contact-line">770-555-4821
        <svg viewBox="0 0 10 10" aria-hidden="true"><path d="M1 3 Q5 0 9 3 L8 4.5 L6.5 3.6 L6.5 3 Q5 2.5 3.5 3 L3.5 3.6 L2 4.5 Z M2.5 5 H7.5 L8.5 9 H1.5 Z"/></svg></p>
      <p class="contact-line">770-555-3067
        <svg viewBox="0 0 10 10" aria-hidden="true"><path d="M2.5 0.5 H7.5 V9.5 H2.5 Z M3.3 1.5 V7.8 H6.7 V1.5 Z" fill-rule="evenodd"/></svg></p>
      <p class="contact-line">dale@tkfenwick.example
        <svg viewBox="0 0 10 10" aria-hidden="true"><path d="M0.5 2 H9.5 V8 H0.5 Z M1 2.4 L5 5.6 L9 2.4 V2.8 L5 6.2 L1 2.8 Z" fill-rule="evenodd"/></svg></p>
      <p class="contact-line">www.tkfenwick.example
        <svg viewBox="0 0 10 10" aria-hidden="true"><circle cx="5" cy="5" r="4.5"/></svg></p>
      <p class="contact-address">4700 West Harbor Boulevard</p>
      <p>Suite #150</p>
      <p>Roswell, GA 30076</p>
    </div>
  </section>

  <section class="card card-back">
    <div class="back-lockup">
      <div class="back-circle"></div>
      <div>
        <p class="back-name">T.K. Fenwick</p>
        <p class="back-tagline">Manufacturing Company, Inc.</p>
        <p class="back-tagline">Since 1918</p>
      </div>
    </div>
  </section>
</body>
</html>
```